Meadow Kr Circle (company name is Meadow Kr Circle LLP)

management of homestay, hospitality something similar with https://www.dorvika.example

Target Market(s)

johor bahru market (Malaysia)

Contact Information for Business Card

Meadow Circle KR LLP

Logo Text

eyes catching, attractive, amazing, Nice, jaw dropping for design

Coding

Coded - Design and coding required

Number of Pages Required

5+ page

Colors

Designer to choose colors to be used in the design.

Requirements
Must have
• please change the short term proposal to our company logo and change the name from dorvika to meadow KR Circle LLP
• thanks
Nice to have
• please let me have eyes catching , jaw dropping design

```html
<!DOCTYPE html>
<html lang="en">
<head>
<meta charset="utf-8">
<title>Meadow Kr Circle – Short-Stay Management</title>
<link rel="stylesheet" href="https://fonts.googleapis.com/css2?family=Lato:wght@400;700;900&family=Open+Sans:wght@400;600;700&display=swap">
<style>
  :root {
    --brown-deep: #2a1c0c;
    --brown-nav: #34240f;
    --brown-accent: #4a3317;
    --ink: #2b1a10;
    --grey-text: #6f6f6f;
    --grey-band: #e6e6e6;
    --white: #ffffff;
    --black: #0d0d0d;
  }
  * { margin: 0; padding: 0; box-sizing: border-box; }
  html, body { width: 1200px; height: 2786px; overflow: hidden; background: var(--white); }
  body { position: relative; font-family: "Lato", sans-serif; color: var(--ink); }

  /* Header */
  .site-header { position: absolute; left: 0; top: 0; width: 1200px; height: 155px; background: var(--white); }
  .brand { position: absolute; left: 0; width: 1200px; top: 95px; text-align: center;
    font-weight: 900; font-size: 30px; letter-spacing: 1px; color: var(--ink); }
  .brand-dot { position: absolute; left: 576px; top: 28px; width: 48px; height: 48px; border-radius: 50%; background: var(--brown-accent); }
  .phone { position: absolute; left: 858px; top: 105px; font-weight: 700; font-size: 22px; color: var(--black); display: flex; align-items: center; gap: 6px; }

  /* Navigation */
  .main-nav { position: absolute; left: 0; top: 155px; width: 1200px; height: 65px; background: var(--brown-nav); border-top: 2px solid #5c4524; }
  .main-nav ul { list-style: none; display: flex; justify-content: center; height: 100%; }
  .main-nav li { display: flex; align-items: center; padding: 0 26px; color: var(--white); font-size: 19px; border-left: 1px solid rgba(255,255,255,0.25); }
  .main-nav li:first-child { border-left: none; }

  /* Hero */
  .hero { position: absolute; left: 0; top: 220px; width: 1200px; height: 542px;
    background: radial-gradient(ellipse at 60% 40%, #a57a43 0%, #6b4a24 30%, #2b1e12 65%, #14100c 100%); }
  .hero-brand { position: absolute; left: 0; top: 170px; width: 1200px; text-align: center; color: var(--white);
    font-weight: 700; font-size: 56px; line-height: 64px; letter-spacing: 2px; }
  .hero-btn { position: absolute; left: 515px; top: 275px; width: 180px; height: 50px; background: var(--brown-deep);
    color: var(--white); font-size: 18px; display: flex; align-items: center; justify-content: center; }
  .dots { position: absolute; left: 566px; top: 492px; display: flex; gap: 10px; }
  .dots span { width: 17px; height: 17px; border-radius: 50%; border: 2px solid var(--white); }
  .dots span.active { background: var(--white); }

  /* About */
  .about { position: absolute; left: 0; top: 762px; width: 1200px; height: 428px; text-align: center; }
  .section-title { font-weight: 400; font-size: 38px; letter-spacing: 1px; color: var(--ink); }
  .about .section-title { position: absolute; top: 75px; width: 100%; }
  .about-text { position: absolute; top: 140px; left: 250px; width: 700px; font-family: "Open Sans", sans-serif;
    font-size: 17px; line-height: 25px; color: var(--grey-text); }
  .outline-btn { position: absolute; display: flex; align-items: center; justify-content: center;
    font-family: "Open Sans", sans-serif; font-weight: 700; font-size: 17px; }
  .about .outline-btn { left: 524px; top: 301px; width: 162px; height: 47px; border: 2px solid var(--brown-accent); color: var(--ink); }

  /* Hospitality */
  .hospitality { position: absolute; left: 0; top: 1190px; width: 1200px; height: 547px; background: var(--brown-deep); overflow: hidden; }
  .hospitality svg { position: absolute; left: 0; top: 0; }
  .hosp-content { position: absolute; left: 168px; top: 88px; width: 400px; color: var(--white); }
  .hosp-content h2 { font-weight: 400; font-size: 32px; line-height: 40px; letter-spacing: 0.5px; margin-bottom: 22px; }
  .hosp-content h3 { font-weight: 700; font-size: 18px; margin-bottom: 8px; }
  .hosp-content p { font-family: "Open Sans", sans-serif; font-size: 14.5px; line-height: 19px; margin-bottom: 24px; }
  .hospitality .outline-btn { left: 171px; top: 407px; width: 163px; height: 50px; border: 2px solid var(--white);
    color: var(--white); font-weight: 400; font-family: "Lato", sans-serif; }

  /* Recent posts */
  .posts { position: absolute; left: 0; top: 1737px; width: 1200px; height: 575px; background: var(--grey-band); }
  .posts .section-title { position: absolute; top: 58px; width: 100%; text-align: center; font-weight: 700; font-size: 32px; letter-spacing: 0; }
  .post-card { position: absolute; top: 135px; width: 280px; height: 346px; background: var(--white); box-shadow: 0 1px 4px rgba(0,0,0,0.12); }
  .post-media { height: 180px; }
  .post-body { padding: 22px 24px 0 24px; }
  .post-body h3 { font-weight: 400; font-size: 20px; color: var(--brown-accent); margin-bottom: 8px; }
  .post-body p { font-family: "Open Sans", sans-serif; font-size: 11px; line-height: 15px; color: #555; margin-bottom: 12px; }
  .post-body .more { font-family: "Open Sans", sans-serif; font-weight: 700; font-size: 14px; color: var(--black); }

  /* Signup */
  .signup { position: absolute; left: 0; top: 2312px; width: 1200px; height: 340px;
    background: linear-gradient(100deg, #3a2a17 0%, #4d3820 40%, #3b2a16 70%, #2a1e10 100%); text-align: center; color: var(--white); }
  .signup h2 { position: absolute; top: 80px; width: 100%; font-weight: 400; font-size: 30px; letter-spacing: 0.5px; }
  .signup p { position: absolute; top: 124px; left: 300px; width: 600px; font-size: 17px; line-height: 24px; }
  .signup-form { position: absolute; left: 276px; top: 194px; width: 632px; height: 57px; display: flex; }
  .email-field { flex: 0 0 461px; background: var(--white); color: var(--ink); display: flex; align-items: center; gap: 10px; padding-left: 20px; font-size: 16px; }
  .subscribe { flex: 1; background: var(--black); color: var(--white); font-weight: 900; font-size: 19px; display: flex; align-items: center; justify-content: center; }

  /* Footer */
  .site-footer { position: absolute; left: 0; top: 2652px; width: 1200px; height: 134px; background: var(--black); color: var(--white); text-align: center; }
  .copyright { position: absolute; top: 46px; width: 100%; font-size: 15px; letter-spacing: 0.5px; }
  .legal { position: absolute; top: 75px; width: 100%; font-size: 12px; }
</style>
</head>
<body>

<header class="site-header">
  <span class="brand-dot" aria-hidden="true"></span>
  <div class="brand">MEADOW KR CIRCLE</div>
  <div class="phone">
    <svg width="22" height="22" viewBox="0 0 24 24" aria-hidden="true"><path fill="#2a1c0c" d="M6.6 10.8a15.1 15.1 0 0 0 6.6 6.6l2.2-2.2c.3-.3.7-.4 1-.2 1.1.4 2.3.6 3.6.6.6 0 1 .4 1 1V20c0 .6-.4 1-1 1C10.6 21 3 13.4 3 4c0-.6.4-1 1-1h3.5c.6 0 1 .4 1 1 0 1.3.2 2.5.6 3.6.1.3 0 .7-.2 1z"/></svg>
    +65 8100 2736
  </div>
</header>

<nav class="main-nav">
  <ul>
    <li>HOME</li><li>ABOUT US</li><li>OUR SERVICES</li><li>WHY US</li><li>BLOGS</li><li>CONTACT</li>
  </ul>
</nav>

<section class="hero" role="img" aria-label="Hotel lobby with a sweeping golden spiral staircase">
  <h1 class="hero-brand">MEADOW KR CIRCLE LLP</h1>
  <div class="hero-btn">CLICK HERE</div>
  <div class="dots"><span></span><span class="active"></span><span></span></div>
</section>

<section class="about">
  <h2 class="section-title">ABOUT US</h2>
  <p class="about-text">We are a short-term rental management and provides hospitality services to help property owners maximise their rental income.<br>Our goal is to help you reap the most from your rental income without you having to do any of the hard work such as handle all the particular renting problems on Staynest, Roomvale, cleaning and dealing with tenants and guests</p>
  <div class="outline-btn">READ MORE</div>
</section>

<section class="hospitality">
  <svg width="1200" height="547" viewBox="0 0 1200 547">
    <defs>
      <linearGradient id="bedroomTone" x1="0" y1="0" x2="1" y2="1">
        <stop offset="0" stop-color="#e9dcc4"/>
        <stop offset="0.5" stop-color="#c7a266"/>
        <stop offset="1" stop-color="#8a5a2c"/>
      </linearGradient>
    </defs>
    <polygon points="722,0 1200,0 1200,547 490,547" fill="url(#bedroomTone)" role="img" aria-label="Ornate bedroom with a gold upholstered bed and chandeliers"/>
  </svg>
  <div class="hosp-content">
    <h2>FULL HOSPITALITY<br>SERVICE</h2>
    <h3>Answering Enquiries, Check-Ins / Outs</h3>
    <p>We will answer all guest’s enquiries, meet them to handover key and verification check. We also provide 24hr on-call support</p>
    <h3>Cleaning, Laundry and Maintenance</h3>
    <p>We get the professional cleaning team to clean up the place after the guest checked-out every time</p>
  </div>
  <div class="outline-btn">READ MORE</div>
</section>

<section class="posts">
  <h2 class="section-title">RECENT POSTS</h2>
  <article class="post-card" style="left:152px">
    <div class="post-media" role="img" aria-label="Dark hotel lounge with warm ceiling lights" style="background:linear-gradient(160deg,#4a3a22,#1c1710 60%,#2f2519)"></div>
    <div class="post-body"><h3>Your Blog Title here</h3><p>massa libero interdum nec interdum vel blandit sed nulla in ullamcorper est eget tempor cursus neque mi consectetuer mi a ultricies massa est sed nisl Class aptent taciti sociosqu ad</p><span class="more">READ MORE</span></div>
  </article>
  <article class="post-card" style="left:458px">
    <div class="post-media" role="img" aria-label="Guests at a bright reception desk with yellow flowers" style="background:linear-gradient(160deg,#d8d0b4,#8c8a55 50%,#4a3b2a)"></div>
    <div class="post-body"><h3>Your Blog Title here</h3><p>massa libero interdum nec interdum vel blandit sed nulla in ullamcorper est eget tempor cursus neque mi consectetuer mi a ultricies massa est sed nisl Class aptent taciti sociosqu ad</p><span class="more">READ MORE</span></div>
  </article>
  <article class="post-card" style="left:763px">
    <div class="post-media" role="img" aria-label="Candlelit restaurant table with wine glasses" style="background:radial-gradient(ellipse at 50% 60%,#6b3b24,#2a1712 60%,#120c0a)"></div>
    <div class="post-body"><h3>Your Blog Title here</h3><p>massa libero interdum nec interdum vel blandit sed nulla in ullamcorper est eget tempor cursus neque mi consectetuer mi a ultricies massa est sed nisl Class aptent taciti sociosqu ad</p><span class="more">READ MORE</span></div>
  </article>
</section>

<section class="signup" role="img" aria-label="Dimly lit hotel bedroom behind a brown overlay">
  <h2>SIGN UP FOR OUR SPECIAL OFFERS</h2>
  <p>Class aptent taciti sociosqu ad litora torquent per conubia nostra per inceptos hymenaeos Proin nulla arcu nonummy luctus dictum eget</p>
  <div class="signup-form">
    <div class="email-field">
      <svg width="20" height="16" viewBox="0 0 20 16" aria-hidden="true"><rect x="1" y="1" width="18" height="14" rx="2" fill="none" stroke="#d94a3a" stroke-width="1.8"/><path d="M1.5 2l8.5 7 8.5-7" fill="none" stroke="#d94a3a" stroke-width="1.8"/></svg>
      Email address
    </div>
    <div class="subscribe">SUBSCRIBE</div>
  </div>
</section>

<footer class="site-footer">
  <div class="copyright">© 2019 COMPANY NAME &nbsp;ALL RIGHT RESERVED</div>
  <div class="legal">TERMS OF USE &nbsp;|&nbsp; PRIVACY POLICY</div>
</footer>

</body>
</html>
```